Design a Website in Wordpress for an Australian Health Training Company in Health related courses

We require a WORDPRESS based Website (due to add on's we need to use for third party software) to replace our old site.
We offer national face to face delivery in medical reception, terminology and also administration.
The website will have around 6 pages and the ability to describe our main 6 courses (perhaps on the Courses page this may be tabs opening up to details for example?)
I have attached a previous sample of a Joomla site which was being developed (please do not feel you have to copy this - but I am just giving it as a sample - copying would be boring). But it gives an idea of look/feel and colours which may be suitable. Open to other ideas though.
I will provide some of the content, but would like the ability to finish the content myself.
Images and graphics are important. While a few medical photos re great - don't be tempted to us all pictures of doctors and nurses (although a couple would be good) - these are administrative courses so general corporate, eye catching visionary pictures of people in general are great. A medical type picture is also fine.
THE BOOKING system - will be via an ADD ON which will occur at the end of the project and is supplied by a third party software company (our student management system). This project will include up to 2 hours working with the Tech guys from the third party software to enable the ADD ON. If this ADD ON requires more time, we will pay hourly (although I do not expect it will).
Target Market(s)
Mostly a female market, many mature aged women target 25-45 yrs. Mixture of medical/health and corporate. Maybe a bit of mums returning to work and corporate inspiration.
Industry/Entity Type
It Company
Coding
Coded - Design and coding required
Number of Pages Required
5+ page
Requirements
Must have
- Wordpress
- Great graphics
- Interesting
- professional and clean
- Enquiry section (info Pak)
- Should have a University feel to it - Education
- Pages
- Home Page - About Us - Recruitment -Courses - Class Schedule - Traineeships Queensland Funding - Latest News Blog - Corporate Training- Contact us

```html
<!DOCTYPE html>
<html lang="en">
<head>
<meta charset="utf-8">
<title>Harbourline Institute of Training</title>
<link rel="stylesheet" href="https://fonts.googleapis.com/css2?family=Cinzel:wght@400;700&family=Lato:ital,wght@0,400;0,700;1,400&display=swap">
<style>
:root{
  --navy:#2d3c5b;
  --navy-dark:#24314c;
  --gold:#c49a5c;
  --gold-light:#d9b781;
  --grey-bg:#ebebeb;
  --text:#333;
  --muted:#666;
  --white:#fff;
}
*{box-sizing:border-box;margin:0;padding:0}
html,body{width:1200px;height:3947px;overflow:hidden}
body{font-family:'Lato',sans-serif;color:var(--text);background:var(--white);font-size:14px;position:relative}
a{color:inherit;text-decoration:none}
ul{list-style:none}
.btn{display:inline-block;background:var(--navy);color:#fff;font-size:13px;padding:9px 26px;border:1px solid var(--navy)}
.section-title{font-family:'Cinzel',serif;text-align:center;font-size:32px;color:var(--navy);letter-spacing:1px}
.section-title .accent{color:var(--gold)}
.section-title::after{content:"";display:block;width:230px;height:2px;background:var(--gold);margin:8px auto 0}

/* top bar */
.topbar{height:40px;background:#e9e9e9;display:flex;align-items:center;padding:0 100px;font-size:12px;color:#555}
.social{display:flex;gap:5px}
.social span{width:20px;height:20px;background:var(--navy);display:block}
.topbar .contact{margin-left:auto;display:flex;gap:22px;align-items:center}
.topbar .contact svg{vertical-align:middle;margin-right:6px}
.topbar .account{margin-left:22px;background:var(--navy);color:#fff;height:40px;display:flex;align-items:center;gap:18px;padding:0 16px;font-weight:700;letter-spacing:.5px}
/* header */
.header{height:97px;display:flex;align-items:center;padding:0 100px}
.brand{display:flex;align-items:center;gap:10px;font-weight:700;color:var(--navy);font-size:15px;line-height:1.15;width:220px}
.brand .mark{width:34px;height:34px;background:var(--navy)}
.nav-main{margin-left:auto;display:flex;gap:38px;font-family:'Cinzel',serif;font-size:14px;color:var(--navy);letter-spacing:1px}
.nav-sub{height:37px;background:var(--navy);display:flex;align-items:center;padding:0 100px;gap:56px;font-family:'Cinzel',serif;color:#fff;font-size:14px;letter-spacing:1px}
.nav-sub .search{margin-left:auto;width:37px;height:37px;background:var(--gold);display:flex;align-items:center;justify-content:center}
/* hero */
.hero{height:516px;position:relative;background:linear-gradient(100deg,#c7b2a0 0%,#e4e8ee 35%,#b9d1e4 55%,#f1ece5 80%,#dcd4cc 100%)}
.hero-strip{position:absolute;left:0;right:0;bottom:0;height:98px;background:rgba(36,49,76,.55)}
.hero-caption{position:absolute;left:0;bottom:0;width:650px;height:98px;background:linear-gradient(90deg,rgba(36,49,76,.92) 60%,rgba(36,49,76,0));color:#fff;padding:18px 100px}
.hero-caption h1{font-size:25px;font-weight:400;letter-spacing:1px}
.hero-caption p{font-size:12.5px;margin-top:6px;line-height:1.4;width:500px}
.hero-arrows{position:absolute;right:100px;bottom:10px;display:flex;gap:8px;color:#fff;font-size:18px}
/* courses */
.courses{height:534px;background:var(--grey-bg);padding-top:40px;position:relative}
.course-row{display:flex;justify-content:center;gap:27px;margin-top:22px}
.course{width:315px;text-align:center}
.course .photo{height:245px;border:4px solid var(--navy);box-shadow:0 6px 10px rgba(0,0,0,.25)}
.course h3{font-family:'Cinzel',serif;font-weight:400;color:var(--navy);font-size:19px;line-height:1.3;margin:18px 0 12px;height:52px;letter-spacing:1px}
.slide-arrow{position:absolute;top:230px}
/* about */
.about{height:324px;padding-top:22px}
.about .intro{width:1000px;margin:20px auto 0;text-align:center;font-size:12.5px;line-height:1.6;color:#444}
.about-cols{display:flex;justify-content:center;gap:60px;margin-top:26px}
.about-col{display:flex;gap:14px;width:290px}
.about-col .ico{width:88px;height:88px;border-radius:50%;background:var(--navy);flex:none;display:flex;align-items:center;justify-content:center;border:5px solid #dde2ea}
.about-col h4{font-family:'Cinzel',serif;color:var(--navy);font-size:18px;margin-top:10px}
.about-col p{font-size:12.5px;line-height:1.45;color:#444;margin-top:4px}
/* why */
.why{height:747px;background:var(--grey-bg);padding-top:28px;position:relative}
.why-emblem{position:absolute;left:130px;top:250px;width:230px;text-align:center;color:var(--navy)}
.why-emblem .name{font-weight:700;font-size:22px;line-height:1.2;letter-spacing:1px}
.why-emblem .seal{width:110px;height:110px;border-radius:50%;background:var(--navy);margin:18px auto 0}
.why svg.arc{position:absolute;left:0;top:0}
.why-item{position:absolute;display:flex;gap:16px;width:520px}
.why-item .ico{width:82px;height:82px;border-radius:50%;background:var(--navy);border:5px solid #fff;flex:none;display:flex;align-items:center;justify-content:center;box-shadow:0 0 0 2px #d0d4da}
.why-item h4{color:var(--navy);font-size:18px;font-weight:700;margin-top:8px}
.why-item p{font-size:14px;line-height:1.4;color:#333}
/* testimonials */
.testimonials{height:345px;padding-top:34px;position:relative}
.avatars{display:flex;justify-content:center;gap:28px;margin-top:26px;align-items:center}
.avatars .av{width:86px;height:86px;border-radius:50%;border:3px solid var(--navy);background:linear-gradient(160deg,#d8c2ad,#8f7560)}
.avatars .arr{color:#bbb;font-size:30px;margin:0 24px}
.quote{width:1000px;margin:24px auto 0;text-align:center;font-style:italic;font-size:13px;line-height:2;color:#333}
.quote .mark{color:#aab3c4;font-size:26px;font-family:'Cinzel',serif;vertical-align:middle}
/* audience */
.audience{height:340px;display:flex;position:relative}
.aud{flex:1;padding:60px 100px 0;color:#fff;position:relative}
.aud.candidate{background:linear-gradient(90deg,#2d3c5b,#3f5078)}
.aud.employer{background:linear-gradient(90deg,#c49a5c,#d8b683);padding-left:150px}
.aud h3{font-family:'Cinzel',serif;font-size:30px;font-weight:400;letter-spacing:1px;display:flex;align-items:center;gap:10px}
.aud .lead{font-weight:700;font-size:13px;margin-top:12px}
.aud p{font-size:13px;line-height:1.5;width:320px;margin-top:4px}
.aud .btn-outline{display:inline-block;border:1px solid #fff;color:#fff;font-size:13px;padding:9px 26px;margin-top:18px}
.aud-seal{position:absolute;left:50%;top:50%;transform:translate(-50%,-50%);width:200px;height:200px;border-radius:50%;background:#fff;border:8px solid rgba(255,255,255,.5);background-clip:padding-box;display:flex;align-items:center;justify-content:center;text-align:center;color:var(--navy);font-weight:700;font-size:17px;line-height:1.25;padding:20px}
/* blog & tweets */
.feeds{height:407px;display:flex;padding:38px 100px 0;gap:58px}
.feed-title{font-family:'Cinzel',serif;font-size:26px;color:var(--navy);display:flex;align-items:center;border-bottom:2px solid var(--gold);padding-bottom:8px}
.feed-title .accent{color:var(--gold);margin-right:8px}
.blog{width:476px}
.blog .title-ctrl{margin-left:auto;font-size:18px;color:#333}
.blog-card{margin-top:40px;border:1px solid #ddd;display:flex;position:relative;height:225px}
.blog-card .photo{width:190px;margin:8px;flex:none;background:linear-gradient(160deg,#dfe5ec,#a8b4c4)}
.blog-card .body{padding:22px 14px 0 6px}
.blog-card h5{font-size:16px;color:#222}
.blog-card p{font-size:13px;line-height:1.4;color:#444;margin-top:4px}
.blog-card .btn-gold{display:inline-block;background:var(--gold);color:#fff;font-size:12px;padding:7px 16px;margin-top:8px}
.date{position:absolute;right:10px;top:-26px;width:60px;height:56px;background:var(--gold);color:#fff;text-align:center;font-size:22px;font-weight:700;line-height:1.1;padding-top:6px}
.date small{display:block;font-size:11px;font-weight:400}
.tweets{flex:1}
.tweets .follow{margin-left:auto;font-family:'Lato',sans-serif;font-size:11px;background:#eef2f6;border:1px solid #ccd;padding:3px 10px;color:#2d3c5b}
.tweet{display:flex;gap:14px;margin-top:26px;font-size:11.5px;line-height:1.35;color:#333;position:relative}
.tweet .ico{width:46px;height:46px;border:1px solid #ccc;flex:none}
.tweet .who{color:#3a76b8;font-weight:700}
.tweet .when{position:absolute;right:0;top:0;color:#777}
.tweet p{width:340px}
/* enrol banner */
.enrol{height:177px;background:linear-gradient(90deg,#dcdfe4,#eef0f2 55%,#e2e0dc);display:flex;align-items:center;padding:0 100px}
.enrol h2{font-weight:700;font-size:25px;line-height:1.45;color:var(--navy);width:780px}
.enrol .booking{margin-left:auto;background:var(--gold);color:#fff;font-size:17px;font-weight:700;padding:18px 40px}
/* footer */
.footer{height:355px;display:flex;background:var(--grey-bg)}
.footer .info{width:470px;padding:32px 0 0 100px}
.footer h4{font-family:'Cinzel',serif;font-size:22px;font-weight:400;letter-spacing:1px}
.info h4{color:var(--navy)}
.info h4::after{content:"";display:block;height:2px;background:var(--navy);margin-top:6px}
.field{height:30px;border:1px solid #bbb;background:#fff;margin-top:10px;font-size:11px;padding:8px;color:#555}
.field.tall{height:70px}
.info .submit{display:inline-block;background:var(--navy);color:#fff;font-weight:700;font-size:13px;padding:10px 28px;margin-top:10px}
.footer .dark{flex:1;background:var(--navy);color:#fff;display:flex;padding:32px 100px 0 60px;gap:50px;clip-path:polygon(20px 0,100% 0,100% 100%,0 100%)}
.quick{width:330px}
.quick h4::after,.contact-col h4::after{content:"";display:block;height:2px;background:#fff;margin-top:6px}
.links{display:flex;gap:40px;margin-top:20px;font-size:12.5px}
.links li{margin-bottom:20px;white-space:nowrap}
.links li::before{content:"•";margin-right:10px}
.contact-col{flex:1}
.c-row{display:flex;gap:12px;margin-top:20px;font-size:12.5px;line-height:1.4;align-items:flex-start;white-space:nowrap}
.c-row svg{flex:none}
.f-social{display:flex;gap:8px;margin-top:22px;padding-left:30px}
.f-social span{width:30px;height:30px;border-radius:50%;background:#fff;display:block}
.copyright{height:28px;background:var(--navy-dark);color:#fff;font-size:11px;text-align:right;padding:8px 170px 0 0}
</style>
</head>
<body>

<div class="topbar">
  <div class="social"><span></span><span></span><span></span><span></span></div>
  <div class="contact">
    <span><svg width="12" height="12" viewBox="0 0 24 24"><path fill="#2d3c5b" d="M6.6 10.8a15 15 0 006.6 6.6l2.2-2.2c.3-.3.7-.4 1-.2 1.1.4 2.3.6 3.6.6.6 0 1 .4 1 1V20c0 .6-.4 1-1 1A17 17 0 013 4c0-.6.4-1 1-1h3.5c.6 0 1 .4 1 1 0 1.3.2 2.5.6 3.6.1.3 0 .7-.2 1z"/></svg>+61 (07) 5550 1842</span>
    <span><svg width="13" height="10" viewBox="0 0 26 20"><rect x="1" y="1" width="24" height="18" fill="none" stroke="#2d3c5b" stroke-width="2"/><path d="M1 1l12 10L25 1" fill="none" stroke="#2d3c5b" stroke-width="2"/></svg>INFO@HARBOURLINE.EXAMPLE</span>
  </div>
  <div class="account"><span>ENGLISH ▾</span><span>LOG IN &nbsp;/&nbsp; REGISTER</span></div>
</div>

<header class="header">
  <div class="brand"><span class="mark"></span><span>Harbourline Institute<br>of Training</span></div>
  <nav class="nav-main"><a>HOME</a><a>ABOUT US</a><a>COURSES</a><a>RECRUITMENT</a><a>CLASS SCHEDULE</a></nav>
</header>
<nav class="nav-sub">
  <a>TRAINEESHIPS QUEENSLAND FUNDING</a><a>LATEST NEWS BLOG</a><a>CORPORATE TRAINING</a><a>CONTACT US</a>
  <span class="search"><svg width="16" height="16" viewBox="0 0 24 24"><circle cx="10" cy="10" r="6.5" fill="none" stroke="#fff" stroke-width="2.5"/><path d="M15 15l6 6" stroke="#fff" stroke-width="2.5"/></svg></span>
</nav>

<section class="hero" role="img" aria-label="Photo of a group of medical staff gathered around reviewing paperwork">
  <div class="hero-strip"></div>
  <div class="hero-caption">
    <h1>Courses for Busy People</h1>
    <p>Our unique FastTrack™ (Combined Assessment &amp; Training) class format delivers accelerated training that's specifically targeted at busy professionals...</p>
  </div>
  <div class="hero-arrows"><span>‹</span><span>›</span></div>
</section>

<section class="courses">
  <h2 class="section-title"><span class="accent">Our</span> Courses</h2>
  <svg class="slide-arrow" style="left:30px" width="24" height="60" viewBox="0 0 24 60"><path d="M20 2L4 30l16 28" fill="none" stroke="#999" stroke-width="2"/></svg>
  <svg class="slide-arrow" style="right:30px" width="24" height="60" viewBox="0 0 24 60"><path d="M4 2l16 28L4 58" fill="none" stroke="#999" stroke-width="2"/></svg>
  <div class="course-row">
    <div class="course">
      <div class="photo" role="img" aria-label="Photo of office staff working together at a desk" style="background:linear-gradient(160deg,#eef0f3,#b7bfc9)"></div>
      <h3>Medical Reception<br>&amp; Terminology</h3>
      <a class="btn">Read More</a>
    </div>
    <div class="course">
      <div class="photo" role="img" aria-label="Photo of a smiling business team" style="background:linear-gradient(160deg,#d6e6f2,#7ea6c4)"></div>
      <h3>Cert III Business<br>Administration</h3>
      <a class="btn">Read More</a>
    </div>
    <div class="course">
      <div class="photo" role="img" aria-label="Photo of a medical terminology book with a stethoscope" style="background:linear-gradient(160deg,#e9d9c3,#b48d70)"></div>
      <h3>Medical<br>Terminology</h3>
      <a class="btn">Read More</a>
    </div>
  </div>
</section>

<section class="about">
  <h2 class="section-title"><span class="accent">About</span> Us</h2>
  <p class="intro">Harbourline is Australia's Leading Provider of Educational, Training and Support Services for the Medical and Dental industry – enabling students to be immediately skilled and 'Job Ready' for a career in Health. Harbourline is a Registered Training Organisation offering specialised Medical Administration Training in over 15 locations Australia wide... [ + ]</p>
  <div class="about-cols">
    <div class="about-col">
      <div class="ico"><svg width="36" height="36" viewBox="0 0 24 24"><path d="M4 4h7a2 2 0 012 2v14a2 2 0 00-2-2H4zM20 4h-5a2 2 0 00-2 2v14a2 2 0 012-2h5z" fill="none" stroke="#fff" stroke-width="1.6"/></svg></div>
      <div><h4>Story</h4><p>Harbourline Health Management started business in February 1999 primarily.... [ + ]</p></div>
    </div>
    <div class="about-col">
      <div class="ico"><svg width="38" height="38" viewBox="0 0 24 24"><path d="M1 12s4-7 11-7 11 7 11 7-4 7-11 7S1 12 1 12z" fill="none" stroke="#fff" stroke-width="1.6"/><circle cx="12" cy="12" r="3.5" fill="#fff"/></svg></div>
      <div><h4>Vision</h4><p>To be Australia's Leading Educational supplier in our Core Units.... [ + ]</p></div>
    </div>
    <div class="about-col">
      <div class="ico"><svg width="38" height="38" viewBox="0 0 24 24"><path d="M2 12l5-5 5 3 5-3 5 5-6 6-4-3-4 3z" fill="none" stroke="#fff" stroke-width="1.6" stroke-linejoin="round"/></svg></div>
      <div><h4>Core Values</h4><p>The Harbourline business is always evolving and as we do, we aim to be true ... [ + ]</p></div>
    </div>
  </div>
</section>

<section class="why">
  <h2 class="section-title"><span class="accent">Why Choose</span> Us</h2>
  <svg class="arc" width="1200" height="747" viewBox="0 0 1200 747">
    <path d="M360 130 Q470 200 480 390 Q470 580 300 660" fill="none" stroke="#c9cbcf" stroke-width="12"/>
    <g fill="#fff" stroke="#999" stroke-width="2">
      <circle cx="370" cy="138" r="8"/><circle cx="452" cy="230" r="8"/><circle cx="478" cy="340" r="8"/>
      <circle cx="476" cy="440" r="8"/><circle cx="440" cy="560" r="8"/><circle cx="370" cy="620" r="8"/><circle cx="315" cy="650" r="8"/>
    </g>
    <g fill="none" stroke="#999" stroke-width="1.5">
      <path d="M378 138 H440 L458 112 H480"/><path d="M460 230 H520 L535 218 H560"/><path d="M486 340 H560 L575 330 H610"/>
      <path d="M484 440 H530 L545 452 H565"/><path d="M448 560 H470"/>
    </g>
  </svg>
  <div class="why-emblem">
    <div class="name">HARBOURLINE INSTITUTE<br>OF TRAINING</div>
    <div class="seal"></div>
  </div>
  <div class="why-item" style="left:458px;top:78px">
    <div class="ico"><svg width="30" height="30" viewBox="0 0 24 24"><circle cx="12" cy="9" r="6" fill="none" stroke="#fff" stroke-width="2"/><path d="M8 14l-2 8 6-3 6 3-2-8" fill="none" stroke="#fff" stroke-width="2"/></svg></div>
    <div><h4>Quality</h4><p>Harbourline delivery quality, effective training facilitated by industry leaders. Just ask our students who rate us on average of 4.7 out of 5.</p></div>
  </div>
  <div class="why-item" style="left:548px;top:176px">
    <div class="ico"><svg width="30" height="30" viewBox="0 0 24 24"><path d="M3 21l4-4M6 12l6 6M9 5l10 10-4 1-7-7z" fill="none" stroke="#fff" stroke-width="2"/></svg></div>
    <div><h4>Experience</h4><p>Harbourline is Australia's largest and leading providers of nationally recognised training in health administration – training from over 17 locations Australia wide.</p></div>
  </div>
  <div class="why-item" style="left:600px;top:288px">
    <div class="ico"><svg width="30" height="30" viewBox="0 0 24 24"><path d="M3 21h18M6 18v-6M11 18V8M16 18v-9M6 9l5-5 4 3 5-4" fill="none" stroke="#fff" stroke-width="2"/></svg></div>
    <div><h4>Value</h4><p>Our innovative teaching approach allows us to deliver exceptional training at affordable prices with no hidden extras.</p></div>
  </div>
  <div class="why-item" style="left:560px;top:404px">
    <div class="ico"><svg width="30" height="30" viewBox="0 0 24 24"><circle cx="12" cy="12" r="4" fill="none" stroke="#fff" stroke-width="2"/><path d="M12 2v4M12 18v4M2 12h4M18 12h4M5 5l3 3M16 16l3 3M19 5l-3 3M8 16l-3 3" stroke="#fff" stroke-width="2"/></svg></div>
    <div><h4>Industry Recognised</h4><p>Harbourline work hand in hand with industry to develop our core programme and consolidate the programme annually to keep the programme fresh and relevant.</p></div>
  </div>
  <div class="why-item" style="left:484px;top:520px">
    <div class="ico"><svg width="30" height="30" viewBox="0 0 24 24"><rect x="3" y="4" width="18" height="14" fill="none" stroke="#fff" stroke-width="2"/><path d="M6 14l4-4 3 3 5-5" fill="none" stroke="#fff" stroke-width="2"/></svg></div>
    <div><h4>Great Job Results</h4><p>Harbourline students get jobs! &nbsp;Our focus is to create job-ready students who are mentored to achieve their goals. &nbsp;Harbourline also provide a recruitment service for industry and graduates.</p></div>
  </div>
</section>

<section class="testimonials">
  <h2 class="section-title"><span class="accent">Clients</span> Testimonials</h2>
  <div class="avatars">
    <span class="arr">‹</span>
    <span class="av" role="img" aria-label="Portrait photo of a client"></span>
    <span class="av" role="img" aria-label="Portrait photo of a client"></span>
    <span class="av" role="img" aria-label="Portrait photo of a client"></span>
    <span class="av" role="img" aria-label="Portrait photo of a client"></span>
    <span class="arr">›</span>
  </div>
  <p class="quote"><span class="mark">“</span> I completed the course on Feb 13th. Loved it. The trainers, Mara and Jo were excellent in their delivery and knowledge. I want to say a huge thank you for the course and knowledge I came away with. I have secured a fantastic job after my first application! Such good value for money too! I would highly recommend it. I'm a mature age person so it's never too late to up-skill yourself to get what you deserve! <span class="mark">”</span></p>
</section>

<section class="audience">
  <div class="aud candidate" role="img" aria-label="Soft navy background photo of a student">
    <h3><svg width="26" height="30" viewBox="0 0 24 28"><circle cx="12" cy="6" r="5" fill="#fff"/><path d="M2 27c0-8 4-12 10-12s10 4 10 12z" fill="#fff"/></svg>For the Candidate</h3>
    <div class="lead">Looking for a Career in Medical Administration?</div>
    <p>Our partner company, Harbourline Institute of Training has been the market leader in Medical Reception Training in Australia for over 17 years. In fact, we pioneered.</p>
    <a class="btn-outline">Read More</a>
  </div>
  <div class="aud employer" role="img" aria-label="Soft gold background photo of an employer at work">
    <h3><svg width="30" height="30" viewBox="0 0 28 28"><circle cx="14" cy="6" r="5" fill="#fff"/><path d="M3 27c0-8 4-12 11-12s11 4 11 12z" fill="#fff"/></svg>For the Employer</h3>
    <p style="margin-top:12px">Harbourline Recruitment is a leading National Health Specialist Recruitment Agency with expertise in Medical and Dental administration recruitment for both permanent and temporary staff.</p>
    <a class="btn-outline">Read More</a>
  </div>
  <div class="aud-seal">Harbourline<br>Institute</div>
</section>

<section class="feeds">
  <div class="blog">
    <div class="feed-title"><span class="accent">Latest</span> Blog <span class="title-ctrl">&lt; &gt;</span></div>
    <div class="blog-card">
      <div class="photo" role="img" aria-label="Photo of a smiling businessman in a suit"></div>
      <div class="body">
        <h5>Lorem ipsum do sit amet,</h5>
        <p>Lorem ipsum dolor sit amet, consectetur adipiscing elit, sed do eiusmod tempor incididunt ut labore et dolore magna aliqua. Ut enim ad minim veniam.</p>
        <a class="btn-gold">Read More</a>
      </div>
      <div class="date">26<small>June</small></div>
    </div>
  </div>
  <div class="tweets">
    <div class="feed-title"><span class="accent">Latest</span> Tweets <span class="follow">Follow</span></div>
    <div class="tweet"><span class="ico"></span><p><span class="who">Clara @claranotes</span><br>Lorem ipsum dolor sit amet, consectetur adipiscing elit, sed di nonummy nibh euismod tincidunt ut laoreet dolore ma</p><span class="when">20 June</span></div>
    <div class="tweet"><span class="ico"></span><p><span class="who">Clara @claranotes</span><br>Lorem ipsum dolor sit amet, consectetur adipiscing elit, sed di nonummy nibh euismod tincidunt ut laoreet dolore ma</p><span class="when">20 June</span></div>
    <div class="tweet"><span class="ico"></span><p><span class="who">Clara @claranotes</span><br>Lorem ipsum dolor sit amet, consectetur adipiscing elit, sed di nonummy nibh euismod tincidunt ut laoreet dolore ma</p><span class="when">20 June</span></div>
  </div>
</section>

<section class="enrol" role="img" aria-label="Faint background photo of a professional office">
  <h2>Enrol In Our HLD40012 Diploma Of Leadership And Managemenr<br>And Gain Vaaluable Skills To Launch Your Management Career.</h2>
  <a class="booking">Booking Now</a>
</section>

<footer class="footer">
  <div class="info">
    <h4>EMAIL me an Info Pack</h4>
    <div class="field">Name</div>
    <div class="field">Email</div>
    <div class="field">Course</div>
    <div class="field tall">State</div>
    <a class="submit">Submit</a>
  </div>
  <div class="dark">
    <div class="quick">
      <h4>Quick Links</h4>
      <div class="links">
        <ul><li>Home</li><li>About Us</li><li>Courses</li><li>Recruitment</li><li>Class Schedule</li><li>Traineeships Queensland Funding</li></ul>
        <ul><li>Latest News Blog</li><li>Corporate Training</li><li>Contact Us</li></ul>
      </div>
    </div>
    <div class="contact-col">
      <h4>Contact Us</h4>
      <div class="c-row"><svg width="18" height="22" viewBox="0 0 24 30"><path d="M12 1a10 10 0 00-10 10c0 8 10 18 10 18s10-10 10-18A10 10 0 0012 1z" fill="#fff"/><circle cx="12" cy="11" r="4" fill="#2d3c5b"/></svg><div><b>Harbour Health Trainings</b><br>123, Ut wisi enim ad minim ve.<br>Mor nostrui tation - 123 456</div></div>
      <div class="c-row"><svg width="18" height="18" viewBox="0 0 24 24"><path fill="#fff" d="M6.6 10.8a15 15 0 006.6 6.6l2.2-2.2c.3-.3.7-.4 1-.2 1.1.4 2.3.6 3.6.6.6 0 1 .4 1 1V20c0 .6-.4 1-1 1A17 17 0 013 4c0-.6.4-1 1-1h3.5c.6 0 1 .4 1 1 0 1.3.2 2.5.6 3.6.1.3 0 .7-.2 1z"/></svg><div>+61 (07) 5550 1842</div></div>
      <div class="c-row"><svg width="18" height="14" viewBox="0 0 26 20"><rect x="1" y="1" width="24" height="18" fill="none" stroke="#fff" stroke-width="2"/><path d="M1 1l12 10L25 1" fill="none" stroke="#fff" stroke-width="2"/></svg><div>info@harbourline.example</div></div>
      <div class="f-social"><span></span><span></span><span></span><span></span></div>
    </div>
  </div>
</footer>
<div class="copyright">Copyright © 2016 Harbour Health Trainings. All Right Reserved</div>

</body>
</html>
```